Business Card Design for Occupational Medicine Start Up Company

We need to design a professional business card. We are a healthcare company providing occupational medicine services to blue collar industries. We are professional, efficient and high quality service providers.

Target Market(s)

Blue Collar Industry: Shipbuilding, Ports, Trucking Companies; The Executives and Safety Officers for these companies

Industry/Entity Type

Healthcare

Contact Information for Business Card

Logo, Name, Title, Email, Phone

Other font styles liked:
• Please match our Brand Guide

Requirements
Must have
• Our Company Colors and Logo

```html
<!DOCTYPE html>
<html lang="en">
<head>
<meta charset="utf-8">
<title>Harborline Clinics – Business Card</title>
<link href="https://fonts.googleapis.com/css2?family=Montserrat:wght@600&family=Arimo:wght@400;700&display=swap" rel="stylesheet">
<style>
  :root {
    --navy: #2b3382;
    --ink: #1c1c1c;
    --paper: #ffffff;
    --backdrop: #e4e4e6;
    --accent-amber: #f1b249;
  }
  * { margin: 0; padding: 0; box-sizing: border-box; }
  html, body { width: 1200px; height: 900px; overflow: hidden; }
  body {
    background: var(--backdrop);
    position: relative;
    font-family: "Arimo", Arial, sans-serif;
  }
  .card {
    position: absolute;
    top: 216px;
    width: 310px;
    height: 502px;
    box-shadow: 2px 3px 6px rgba(0,0,0,0.35);
  }
  .card-front {
    left: 279px;
    background: var(--navy);
    border-radius: 0 62px 0 62px;
  }
  .card-back {
    left: 617px;
    background: var(--paper);
    border-radius: 62px 0 62px 0;
  }
  .brand {
    position: absolute;
    left: 0; right: 0;
    text-align: center;
    font-family: "Montserrat", Arial, sans-serif;
    font-weight: 600;
  }
  .brand-dot {
    display: block;
    margin: 0 auto 14px;
    border-radius: 50%;
  }
  .brand-name { display: block; font-size: 25px; letter-spacing: 0.5px; line-height: 1.1; }
  .brand-sub { display: block; font-size: 15px; letter-spacing: 5px; margin-top: 4px; }
  .card-front .brand { top: 318px; color: var(--paper); }
  .card-front .brand-dot { width: 60px; height: 60px; background: var(--paper); }
  .card-back .brand { top: 74px; color: var(--navy); }
  .card-back .brand-dot { width: 66px; height: 66px; background: var(--navy); margin-bottom: 20px; }

  .person { position: absolute; left: 32px; top: 308px; }
  .person-name { color: var(--navy); font-weight: 700; font-size: 20px; line-height: 1; }
  .person-title { color: var(--ink); font-size: 15px; margin-top: 3px; }
  .contact-list { list-style: none; position: absolute; left: 32px; top: 360px; color: var(--ink); font-size: 14px; }
  .contact-list li { display: flex; align-items: center; height: 18px; }
  .contact-list svg { width: 12px; height: 12px; margin-right: 6px; fill: var(--navy); }
  .address { position: absolute; left: 33px; top: 430px; font-size: 14px; line-height: 18px; color: var(--ink); }
</style>
</head>
<body>
  <section class="card card-front">
    <div class="brand">
      <span class="brand-dot"></span>
      <span class="brand-name">HARBORLINE</span>
      <span class="brand-sub">CLINICS</span>
    </div>
  </section>

  <section class="card card-back">
    <div class="brand">
      <span class="brand-dot"></span>
      <span class="brand-name">HARBORLINE</span>
      <span class="brand-sub">CLINICS</span>
    </div>

    <div class="person">
      <p class="person-name">DANIEL MERCER</p>
      <p class="person-title">MANAGING DIRECTOR</p>
    </div>

    <ul class="contact-list">
      <li>
        <svg viewBox="0 0 24 24" aria-hidden="true"><path d="M6.6 10.8a15.1 15.1 0 0 0 6.6 6.6l2.2-2.2c.3-.3.7-.4 1-.2 1.1.4 2.3.6 3.6.6.6 0 1 .4 1 1V20c0 .6-.4 1-1 1A17 17 0 0 1 3 4c0-.6.4-1 1-1h3.5c.6 0 1 .4 1 1 0 1.3.2 2.5.6 3.6.1.3 0 .7-.2 1z"/></svg>
        055-210 734 618
      </li>
      <li>
        <svg viewBox="0 0 24 24" aria-hidden="true"><path d="M2 5h20v14H2z M2 5l10 8 10-8" fill="var(--navy)" stroke="#fff" stroke-width="1.5"/></svg>
        hello@harborline.example
      </li>
      <li>
        <svg viewBox="0 0 24 24" aria-hidden="true"><circle cx="12" cy="12" r="10"/><path d="M2 12h20M12 2c3 3 3 17 0 20M12 2c-3 3-3 17 0 20M4 7h16M4 17h16" stroke="#fff" stroke-width="1.3" fill="none"/></svg>
        www.harborline.example
      </li>
    </ul>

    <p class="address">87, Quayside Road Unit 4<br>30718,Portland Bay</p>
  </section>
</body>
</html>
```